Counseling Practice Business Card

I need a professional looking business card incorporating my new logo that was just completed. Card needs to incorporate my name and title, description of my specialty, my address, my phone number, my fax number, my email and my website URL. I need to be able to choose design on/with different paper colors and textures.
I do not have a lot of business card ideas so I am open to anything but I want bold,sharp, clear card without additional designs other than my logo (see attached file info). I am open to different color backgrounds or paper colors including black. I do not like traditional brackets around area codes in phone number or dashes between numbers in phone number. Am open to other ways of presenting including periods between numbers as appropriate. I do not know enough to know what I like yet but I want card to coordinate and work together with my logo. My practice emphasizes natural mental health interventions so any use of color (with background paper color or the blue and green in my logo) that elicits nature is nice. In addition to black, any natural brown or wood looking background might be desirable also. Most of the offerings so far look very similar and boring.

Target Market(s)

Potential therapy clients and other professionals

Contact Information for Business Card

Card information:
Gerald M. Whitcombe, Ph.D.
Licensed Clinical Psychologist
Integrative Health Coach
4812 Marlowe Ridge Blvd SE
Suite 310
Alder Falls, GA 30584
(770) 415-2983 phone
(770) 581-4096 fax
drgeraldwhitcombe@quillmarsh.net
brightfernwellness.net

Font styles to use
Serif
Sans Serif
Other font styles liked:
• anything that you think looks crisp, clear and easily readable

Requirements
Must have
• Any color used should coordinate with my logo design (see attached files).
• Card should be printed horizontally so top and bottom are longest sides of rectangle.
• Background color or paper color should complement and highlight logo. Do not like a white background. black, grey, brown or any color my logo would blend well with.
Nice to have
• I would like designer to utilize color to highlight letters/name or phone-fax-web symbols.
• Bottom edge of card could be highlighted if appropriate to an idea.
Should not have
• I would NOT want the card to have a pure white background at all.
• No clear cards.
• Cards should be oriented with long sides on bottom and top, NOT sides. DO NOT LIKE THIS THIN TALL ORIENTATION.

```html
<!DOCTYPE html>
<html lang="en">
<head>
<meta charset="utf-8">
<title>Brightfern Wellness – Business Card</title>
<link href="https://fonts.googleapis.com/css2?family=Open+Sans:wght@400;600;700&display=swap" rel="stylesheet">
<style>
  :root {
    --backdrop: #2b2b2c;
    --card: #151618;
    --blue: #2a7bc4;
    --green: #1d7a3c;
    --text: #c9cacc;
    --muted: #b5b6b8;
  }
  * { margin: 0; padding: 0; box-sizing: border-box; }
  html, body { width: 1200px; height: 960px; overflow: hidden; }
  body {
    background: var(--backdrop);
    font-family: "Open Sans", Arial, sans-serif;
    position: relative;
  }
  .card {
    position: absolute;
    left: 322px;
    width: 600px;
    background: var(--card);
    box-shadow: 0 6px 18px rgba(0,0,0,.55);
  }
  .card--front { top: 108px; height: 344px; }
  .card--back { top: 494px; height: 342px; }

  .identity { position: absolute; left: 30px; top: 29px; }
  .identity__name {
    color: var(--blue);
    font-weight: 700;
    font-size: 18px;
    letter-spacing: .2px;
    text-transform: uppercase;
    line-height: 24px;
  }
  .identity__title { color: var(--green); font-size: 14.5px; line-height: 21px; }

  .address {
    position: absolute; left: 30px; top: 172px;
    color: var(--text); font-size: 14.5px; line-height: 20px;
    font-style: normal;
  }
  .contacts { position: absolute; left: 30px; top: 237px; list-style: none; }
  .contacts li {
    display: flex; align-items: center;
    color: var(--text); font-size: 14.5px; line-height: 19.5px;
    white-space: nowrap;
  }
  .contacts svg { width: 14px; height: 14px; margin-right: 10px; flex: none; fill: var(--blue); }

  .brand { display: flex; align-items: center; color: var(--blue); font-weight: 600; white-space: nowrap; }
  .brand__dot { border-radius: 50%; background: var(--green); flex: none; }
  .brand--small { position: absolute; right: 30px; top: 254px; font-size: 22px; }
  .brand--small .brand__dot { width: 13px; height: 13px; margin-right: 9px; }
  .brand--large { position: absolute; left: 0; right: 0; top: 140px; justify-content: center; font-size: 44px; }
  .brand--large .brand__dot { width: 26px; height: 26px; margin-right: 18px; }

  .edge { position: absolute; left: 0; bottom: 0; width: 100%; height: 10px; display: flex; gap: 2px; }
  .edge__blue { flex: 319; background: var(--blue); }
  .edge__green { flex: 279; background: var(--green); }

  .web-line {
    position: absolute; left: 0; right: 0; top: 283px; text-align: center;
    color: var(--muted); font-size: 14.5px; letter-spacing: 3.6px;
  }
</style>
</head>
<body>
  <section class="card card--front">
    <div class="identity">
      <h1 class="identity__name">Gerald M. Whitcombe, Ph.D.</h1>
      <p class="identity__title">Licensed Clinical Psychologist</p>
      <p class="identity__title">Integrative Health Coach</p>
    </div>
    <address class="address">
      4812 Marlowe Ridge Blvd SE<br>
      Suite 310<br>
      Alder Falls, GA 30584
    </address>
    <ul class="contacts">
      <li><svg viewBox="0 0 16 16" aria-hidden="true"><path d="M1 5c0-2 3-3 7-3s7 1 7 3v1h-3V5H4v1H1z M3 7h10l1 7H2z M6 9h4v3H6z"/></svg>(770) 415-2983</li>
      <li><svg viewBox="0 0 16 16" aria-hidden="true"><path d="M4 1h8v4H4z M1 6h14v6h-3v-2H4v2H1z M4 11h8v4H4z"/></svg>(770) 581-4096</li>
      <li><svg viewBox="0 0 16 16" aria-hidden="true"><path d="M1 3h14v1L8 9 1 4z M1 6l7 5 7-5v7H1z"/></svg>drgeraldwhitcombe@quillmarsh.net</li>
      <li><svg viewBox="0 0 16 16" aria-hidden="true"><circle cx="8" cy="8" r="7"/><path d="M5 4c2 1 2 3 0 4s1 3 3 2M11 3c-1 2 1 3 2 3" stroke="#151618" stroke-width="1.3" fill="none"/></svg>www.brightfernwellness.net</li>
    </ul>
    <div class="brand brand--small"><span class="brand__dot"></span>Brightfern Wellness</div>
    <div class="edge"><span class="edge__blue"></span><span class="edge__green"></span></div>
  </section>

  <section class="card card--back">
    <div class="brand brand--large"><span class="brand__dot"></span>Brightfern Wellness</div>
    <p class="web-line">www.brightfernwellness.net</p>
  </section>
</body>
</html>
```